Business Cards for IT Consulting Company (Managed Service Provider)

I am looking to have some business cards printed and would like some designs. We are an IT Consulting company based in Vancouver BC. I would like a nice clean and modern look to the cards. I have uploaded all the versions of my logo so parts can be used as needed. Here is a snippit from our website homepage:

Quillbrook Networks Ltd. is an IT Solutions Partner located in Vancouver BC, Canada. We offer IT solutions and support to customers in the greater Vancouver Area. With expertise in Microsoft platforms, as well as Linux and Mac OSX and over 12 years experience in the IT industry, Quillbrook Networks is dedicated to offering our clients top quality service and products. We take pride in the solutions we offer our customers. The greatest compliment a client can give us is to recommend our services.

Quillbrook Networks Ltd. offers a wide range of IT services from onsite service to remote support and managed service solutions. This allows clients to choose the support path that best suits their company’s needs. Supporting many different sized companies from small to enterprise level over the past 12 years Quillbrook Networks has the experience and expertise needed to ensure things run smoothly. Allowing our clients to focus on doing business.

Revolutionizing the way IT services are delivered.

Quillbrook Networks is dedicated to providing our clients with IT solutions that work and grow with them for years to come. This philosophy helps save money in the long run instead of replacing equipment constantly. Far too often IT solutions are not well thought out and while possibly solving the problem at hand, require replacement due to growth or quality within a very short time frame. Quillbrook Networks takes pride in providing solutions that will last and be able to accommodate growth without the need for replacement.

Industry/Entity Type

Information Technology

Contact Information for Business Card

Quillbrook Networks Ltd.
(Employee Name)
Eml: (Employees Email Address)
Web: quillbrook.me
Ph: 604-555-0148

Font styles to use
Serif
Sans Serif

Requirements
Must have
• The Company logo and company colors.
Nice to have
• - Our tag line: "Revolutionizing IT Services" or "Revolutionizing the way IT services are delivered."
• - Also I really like the idea of nature and technology together blending which is sort of where my logo came from so integrating that somehow onto the business cards would be great.

```html
<!DOCTYPE html>
<html lang="en">
<head>
<meta charset="utf-8">
<title>Quillbrook Networks Ltd. — Business Cards</title>
<link rel="stylesheet" href="https://fonts.googleapis.com/css2?family=Questrial&display=swap">
<style>
  :root {
    --backdrop: #2d2d2d;
    --brand-blue: #35a8e0;
    --paper: #ffffff;
    --ink: #2b2b2b;
    --ink-soft: #555555;
  }
  html, body {
    margin: 0;
    padding: 0;
    width: 1200px;
    height: 1114px;
    overflow: hidden;
    background: var(--backdrop);
    font-family: "Questrial", "Century Gothic", sans-serif;
  }
  .canvas {
    position: relative;
    width: 1200px;
    height: 1114px;
  }
  .card {
    position: absolute;
    left: 150px;
    width: 900px;
    height: 514px;
    box-sizing: border-box;
    box-shadow: 0 10px 30px rgba(0,0,0,0.35);
  }
  .card--front { top: 28px; background: var(--brand-blue); color: var(--paper); }
  .card--back { top: 572px; background: var(--paper); color: var(--ink); }

  /* Front */
  .front-mark {
    position: absolute;
    left: 0; right: 0;
    top: 170px;
    display: flex;
    justify-content: center;
    align-items: center;
    gap: 22px;
  }
  .front-mark__square {
    width: 58px; height: 58px;
    border: 3px solid var(--paper);
    box-sizing: border-box;
  }
  .front-mark__name {
    font-size: 62px;
    line-height: 1;
    letter-spacing: 1px;
    color: var(--paper);
  }
  .front-mark__name small {
    display: block;
    font-size: 24px;
    letter-spacing: 3px;
    margin-top: 8px;
  }
  .tagline {
    position: absolute;
    left: 0; right: 0;
    bottom: 56px;
    text-align: center;
    font-size: 24px;
    letter-spacing: 1.5px;
  }

  /* Back */
  .back-mark {
    position: absolute;
    left: 60px;
    top: 250px;
    display: flex;
    align-items: center;
    gap: 16px;
    color: var(--brand-blue);
  }
  .back-mark__square {
    width: 40px; height: 40px;
    border: 2px solid var(--brand-blue);
    box-sizing: border-box;
  }
  .back-mark__name {
    font-size: 44px;
    line-height: 1;
  }
  .back-mark__name small {
    display: block;
    font-size: 17px;
    letter-spacing: 2.5px;
    margin-top: 6px;
  }
  .contact {
    position: absolute;
    right: 60px;
    top: 140px;
    text-align: right;
  }
  .contact__name {
    font-size: 28px;
    color: var(--brand-blue);
    margin: 0;
  }
  .contact__role {
    font-size: 20px;
    color: var(--ink-soft);
    margin: 4px 0 28px;
  }
  .contact__list {
    list-style: none;
    margin: 0;
    padding: 0;
    font-size: 21px;
    line-height: 1.7;
  }
  .contact__list li {
    display: flex;
    justify-content: flex-end;
    align-items: center;
    gap: 12px;
  }
  .contact__icon {
    width: 18px; height: 18px;
    fill: none;
    stroke: var(--brand-blue);
    stroke-width: 2;
  }
</style>
</head>
<body>
<main class="canvas">
  <section class="card card--front" aria-label="Card front">
    <div class="front-mark">
      <span class="front-mark__square"></span>
      <div class="front-mark__name">quillbrook<small>NETWORKS LTD.</small></div>
    </div>
    <p class="tagline">Revolutionizing the way IT services are delivered</p>
  </section>

  <section class="card card--back" aria-label="Card back">
    <div class="back-mark">
      <span class="back-mark__square"></span>
      <div class="back-mark__name">quillbrook<small>NETWORKS LTD.</small></div>
    </div>
    <div class="contact">
      <p class="contact__name">Dana Whitlow</p>
      <p class="contact__role">Network Engineer</p>
      <ul class="contact__list">
        <li>604-555-0148
          <svg class="contact__icon" viewBox="0 0 20 20"><path d="M5 2h3l1.5 4-2 1.5a10 10 0 0 0 5 5l1.5-2 4 1.5v3a2 2 0 0 1-2 2A16 16 0 0 1 3 4a2 2 0 0 1 2-2z"/></svg>
        </li>
        <li>dwhitlow@quillbrook.me
          <svg class="contact__icon" viewBox="0 0 20 20"><rect x="2" y="4" width="16" height="12"/><path d="M2 4l8 7 8-7"/></svg>
        </li>
        <li>www.quillbrook.me
          <svg class="contact__icon" viewBox="0 0 20 20"><circle cx="10" cy="10" r="8"/><ellipse cx="10" cy="10" rx="3.5" ry="8"/><path d="M2 10h16"/></svg>
        </li>
      </ul>
    </div>
  </section>
</main>
</body>
</html>
```